Restyle corporate identity (+ logo) for a road construction company

We need a new logo and stationary design for our company VARNOK path. VARNOK path® increases the road base strength, while reducing major costs and time of road construction. Attached some examples of the current design.

Our wishes for the new logo:
- Business look
- Style sheet
- Modern

More information: www.varnokpath.example
Updates

Target Market(s)

Government

Industry/Entity Type

Construction

Requirements
Must have
• Logo (with road sign) + text

```html
<!DOCTYPE html>
<html lang="en">
<head>
<meta charset="utf-8">
<title>VARNOK path – Business Card</title>
<link rel="stylesheet" href="https://fonts.googleapis.com/css2?family=Open+Sans:wght@400;600&display=swap">
<style>
  :root {
    --brand-blue: #1f7fe3;
    --backdrop: #7f7f7f;
    --card-white: #f4f5f6;
    --text-grey: #5a5a5a;
    --muted-grey: #8a8a8a;
    --rule-grey: #555555;
    --road-tint: #d3e3f1;
    --white: #ffffff;
  }
  * { margin: 0; padding: 0; box-sizing: border-box; }
  html, body {
    width: 1105px; height: 1200px; overflow: hidden;
    background: var(--backdrop);
    font-family: "Open Sans", Arial, sans-serif;
  }
  .card {
    position: absolute; left: 172px;
    width: 760px; height: 434px; overflow: hidden;
  }
  /* Front */
  .card-front { top: 110px; background: var(--card-white); }
  .side-band {
    position: absolute; left: 0; top: 0;
    width: 111px; height: 100%; background: var(--brand-blue);
  }
  .road-decoration {
    position: absolute; right: 0; top: 0;
    width: 330px; height: 100%;
    background: linear-gradient(90deg, rgba(211,227,241,0) 0%, var(--road-tint) 45%, var(--road-tint) 100%);
    opacity: 0.7;
  }
  .wordmark {
    position: absolute; left: 58px; top: 62px;
    display: flex; align-items: center; gap: 18px;
  }
  .wordmark-square {
    width: 62px; height: 62px; background: var(--white);
    border: 3px solid var(--brand-blue); border-radius: 8px;
  }
  .wordmark-name {
    font-weight: 600; font-size: 46px; line-height: 1;
    color: var(--brand-blue); letter-spacing: 1px;
  }
  .person-name {
    position: absolute; left: 171px; top: 212px;
    font-size: 26px; font-weight: 600; color: var(--brand-blue);
    letter-spacing: 0.5px;
  }
  .person-role {
    position: absolute; left: 171px; top: 250px;
    font-size: 20px; color: var(--muted-grey);
  }
  .contact-list {
    position: absolute; left: 171px; top: 302px;
    list-style: none; font-size: 19px; color: var(--text-grey);
  }
  .contact-list li {
    display: flex; align-items: center; gap: 10px; height: 28px;
  }
  .contact-icon { width: 17px; height: 17px; fill: var(--brand-blue); flex: none; }
  .contact-divider {
    position: absolute; left: 434px; top: 303px;
    width: 1.5px; height: 77px; background: var(--rule-grey);
  }
  .address {
    position: absolute; left: 458px; top: 302px;
    font-style: normal; font-size: 19px; line-height: 28px; color: var(--text-grey);
  }
  /* Back */
  .card-back { top: 640px; background: var(--brand-blue); }
  .wordmark-back {
    position: absolute; left: 0; right: 0; top: 180px;
    display: flex; justify-content: center; align-items: center; gap: 18px;
  }
  .wordmark-back .wordmark-square { background: var(--white); border-color: var(--white); }
  .wordmark-back .wordmark-name { color: var(--white); }
  .back-url {
    position: absolute; left: 0; right: 0; top: 364px;
    text-align: center; font-size: 20px; color: var(--white);
    letter-spacing: 4px;
  }
</style>
</head>
<body>
  <section class="card card-front">
    <div class="side-band"></div>
    <div class="road-decoration" role="img" aria-label="Faint road motif decoration"></div>
    <div class="wordmark">
      <span class="wordmark-square"></span>
      <span class="wordmark-name">VARNOK path</span>
    </div>
    <h1 class="person-name">DAAN VERHOEF</h1>
    <p class="person-role">CEO/Founder</p>
    <ul class="contact-list">
      <li>
        <svg class="contact-icon" viewBox="0 0 24 24" aria-hidden="true"><path d="M6.6 10.8a15.1 15.1 0 0 0 6.6 6.6l2.2-2.2a1 1 0 0 1 1-.25 11.4 11.4 0 0 0 3.6.57 1 1 0 0 1 1 1V20a1 1 0 0 1-1 1A17 17 0 0 1 3 4a1 1 0 0 1 1-1h3.5a1 1 0 0 1 1 1c0 1.25.2 2.45.57 3.57a1 1 0 0 1-.25 1z"/></svg>
        612 408 7751
      </li>
      <li>
        <svg class="contact-icon" viewBox="0 0 24 24" aria-hidden="true"><path d="M2 5h20v14H2z M3.5 6.5 12 12.5l8.5-6" fill="var(--brand-blue)"/><path d="M3 6.5 12 13l9-6.5" fill="none" stroke="#f4f5f6" stroke-width="1.6"/></svg>
        info@varnokpath.example
      </li>
      <li>
        <svg class="contact-icon" viewBox="0 0 24 24" aria-hidden="true"><circle cx="12" cy="12" r="10"/><path d="M2 12h20M12 2c3 3 3 17 0 20M12 2c-3 3-3 17 0 20" fill="none" stroke="#f4f5f6" stroke-width="1.4"/></svg>
        www.varnokpath.example
      </li>
    </ul>
    <div class="contact-divider"></div>
    <address class="address">
      Lindenhofstraat 58<br>
      3512 KV Utrecht<br>
      The Netherlands
    </address>
  </section>

  <section class="card card-back">
    <div class="wordmark wordmark-back">
      <span class="wordmark-square"></span>
      <span class="wordmark-name">VARNOK path</span>
    </div>
    <p class="back-url">www.varnokpath.example</p>
  </section>
</body>
</html>
```